Business Card for brovaLINK

Create a Business Card with an existing logo for brovaLINK AG. We are a Information Technology company that does consulting and developing SW to automate business processes. The main colors are given from the logo.

Industry/Entity Type

Business

Requirements
Nice to have
• we use a a font style Century Gothic in our documents

```html
<!DOCTYPE html>
<html lang="en">
<head>
<meta charset="utf-8">
<title>brovaLINK AG – Business Card</title>
<link href="https://fonts.googleapis.com/css2?family=Didact+Gothic&family=Questrial&display=swap" rel="stylesheet">
<style>
  :root{
    --stage:#ecebe8;
    --white:#ffffff;
    --ink:#3a3d42;
    --blue-deep:#1f3f9e;
    --blue:#2a6fd0;
    --blue-light:#3fa2e6;
    --green:#2bb24a;
    --green-light:#8fd23a;
    --lavender:#c9d2ec;
    --lavender-soft:#e4e8f5;
  }
  *{margin:0;padding:0;box-sizing:border-box}
  html,body{width:1200px;height:1024px;overflow:hidden}
  body{background:var(--stage);font-family:"Didact Gothic","Questrial",sans-serif;position:relative}
  .card{position:absolute;width:600px;height:340px;border-radius:26px;overflow:hidden;
    box-shadow:0 10px 30px rgba(0,0,0,.18)}
  .card svg.bg{position:absolute;inset:0}
  .card-front{left:90px;top:110px;background:var(--white)}
  .card-back{left:510px;top:560px}

  .brand{position:absolute;display:flex;align-items:center;gap:12px;color:var(--ink);font-size:44px;line-height:1}
  .brand-dot{width:30px;height:30px;border-radius:50%;background:var(--blue)}
  .card-front .brand{left:40px;top:150px}

  .holder{position:absolute;left:400px;top:38px}
  .holder-name{color:var(--blue);font-size:20px;font-weight:700;font-family:"Questrial",sans-serif}
  .holder-role{color:var(--green);font-size:13px;margin-top:2px}

  .contact{position:absolute;left:372px;top:168px;list-style:none;color:var(--white);font-size:14.5px;line-height:22px}
  .contact li{display:flex;align-items:center;gap:8px}
  .contact svg{width:12px;height:12px;flex:none}

  .address{position:absolute;left:40px;top:286px;display:flex;gap:8px;color:var(--white);font-size:14.5px;line-height:20px}
  .address svg{width:12px;height:14px;margin-top:3px;flex:none}

  .card-back .brand{left:170px;top:130px;color:var(--white);font-size:56px}
  .card-back .brand-dot{width:40px;height:40px;background:var(--green)}
  .back-url{position:absolute;left:176px;top:200px;color:var(--white);font-size:13px;opacity:.9}
</style>
</head>
<body>

<section class="card card-front" aria-label="Business card front">
  <svg class="bg" viewBox="0 0 600 340" preserveAspectRatio="none">
    <defs>
      <linearGradient id="frontBlue" x1="0" y1="1" x2="1" y2="0">
        <stop offset="0" stop-color="var(--blue-deep)"/>
        <stop offset=".6" stop-color="var(--blue)"/>
        <stop offset="1" stop-color="var(--blue-light)"/>
      </linearGradient>
      <linearGradient id="frontGreen" x1="0" y1="1" x2="1" y2="0">
        <stop offset="0" stop-color="var(--green)"/>
        <stop offset="1" stop-color="var(--green-light)"/>
      </linearGradient>
    </defs>
    <path d="M0,248 C190,244 290,170 370,100 C450,30 530,18 600,22 L600,340 L0,340 Z" fill="url(#frontGreen)"/>
    <path d="M0,268 C190,266 300,196 380,126 C460,58 530,44 600,46 L600,340 L0,340 Z" fill="var(--white)"/>
    <path d="M0,274 C190,272 302,202 384,132 C462,64 532,50 600,52 L600,340 L0,340 Z" fill="url(#frontBlue)"/>
  </svg>

  <div class="brand"><span class="brand-dot"></span><span class="brand-name">brovaLINK</span></div>

  <div class="holder">
    <div class="holder-name">Lukas Brenner</div>
    <div class="holder-role">CEO</div>
  </div>

  <ul class="contact">
    <li><svg viewBox="0 0 12 12"><path d="M2 1h2l1 3-1.5 1a7 7 0 0 0 3.5 3.5L8 7l3 1v2a1 1 0 0 1-1 1A9 9 0 0 1 1 2a1 1 0 0 1 1-1z" fill="var(--green-light)"/></svg>+41 56 210 48 93</li>
    <li><svg viewBox="0 0 12 12"><rect x="3" y="0.5" width="6" height="11" rx="1.2" fill="var(--green-light)"/></svg>+41 79 456 20 17</li>
    <li><svg viewBox="0 0 12 12"><rect x="0.5" y="2" width="11" height="8" rx="1" fill="var(--green-light)"/><path d="M1 2.5 6 6.5 11 2.5" stroke="var(--blue)" fill="none"/></svg>lukas.brenner@brovalink.ch</li>
    <li><svg viewBox="0 0 12 12"><circle cx="6" cy="6" r="5.5" fill="var(--green-light)"/><path d="M.5 6h11M6 .5c-2.5 3-2.5 8 0 11M6 .5c2.5 3 2.5 8 0 11" stroke="var(--blue)" fill="none" stroke-width=".8"/></svg>www.brovalink.ch</li>
  </ul>

  <div class="address">
    <svg viewBox="0 0 12 14"><path d="M6 0a5 5 0 0 1 5 5c0 4-5 9-5 9S1 9 1 5a5 5 0 0 1 5-5z" fill="var(--green-light)"/><circle cx="6" cy="5" r="2" fill="var(--blue)"/></svg>
    <span>Lindenweg 12, 5400 Baden,<br>Switzerland</span>
  </div>
</section>

<section class="card card-back" aria-label="Business card back">
  <svg class="bg" viewBox="0 0 600 340" preserveAspectRatio="none">
    <defs>
      <linearGradient id="backBase" x1="0" y1="0" x2="1" y2="1">
        <stop offset="0" stop-color="var(--lavender)"/>
        <stop offset="1" stop-color="var(--lavender-soft)"/>
      </linearGradient>
      <linearGradient id="backRibbon" x1="0" y1="0" x2="1" y2="1">
        <stop offset="0" stop-color="var(--blue)"/>
        <stop offset=".5" stop-color="var(--blue-light)"/>
        <stop offset="1" stop-color="var(--green)"/>
      </linearGradient>
    </defs>
    <rect width="600" height="340" fill="url(#backBase)"/>
    <path d="M470,0 C520,10 570,30 600,60 L600,0 Z" fill="var(--blue-deep)"/>
    <path d="M0,0 L300,0 C230,60 230,150 300,200 C370,250 470,250 600,220 L600,340 L360,340 C300,300 200,280 150,220 C90,150 110,60 0,40 Z" fill="url(#backRibbon)" opacity=".85"/>
    <path d="M300,0 C230,60 230,150 300,200 C370,250 470,250 600,220" stroke="var(--white)" stroke-width="3" fill="none" opacity=".6"/>
  </svg>

  <div class="brand"><span class="brand-name">brovaLINK</span><span class="brand-dot"></span></div>
  <div class="back-url">www.brovalink.ch</div>
</section>

</body>
</html>
```